SLides. Repair phone, tablet, pc, accessories seell and tempered glass.

i would like to show client what we do . what we sell. the repair can be done from 30min. We install tempered glasses. We sell accessories. have already slides. but design not very modern. need to change them. https://filebox.example/folders/7KpQw2XzLm9RtYvBn4HcJd8SfGaEuW3?usp=sharing https://filebox.example/folders/4TzXk-Lp83QnVHcdRw9yFmPoGsa?usp=sharing i send all the design i have. our website is www.nutikoda.ee i uploaded what photos i like.

Target Market(s)

Trade buy repair. phones, taböets, PC, sell accessories. show all services

Colors

Designer to choose colors to be used in the design.

Requirements
Must have
• modern design modern phone pictures. zeno pictures vexa pictures. To emphasize our style.
Nice to have
• modern pictures of our services. and modern pictures of goods.
Should not have
• non modern pictures and

```html
<!DOCTYPE html>
<html lang="en">
<head>
<meta charset="utf-8">
<title>Nutikoda — Slides</title>
<link href="https://fonts.googleapis.com/css2?family=Ubuntu:wght@400;500;700&family=Yanone+Kaffeesatz:wght@300&display=swap" rel="stylesheet">
<style>
  :root {
    --page: #ffffff;
    --cyan-1: #2ad6f0;
    --cyan-2: #3bbde8;
    --cyan-text: #1fb6e0;
    --ink: #1c1c1c;
    --ink-soft: #555555;
    --bar: #ffffff;
    --repair-bg: #eef1f4;
    --badge-dark: #111111;
    --badge-light: #ffffff;
  }
  * { margin: 0; padding: 0; box-sizing: border-box; }
  html, body { width: 1200px; height: 2266px; overflow: hidden; background: var(--page); }
  body { position: relative; font-family: "Ubuntu", sans-serif; }

  .slide {
    position: absolute; left: 64px; width: 1065px; height: 553px; overflow: hidden;
    box-shadow: 0 6px 22px rgba(0,0,0,0.10);
  }
  .slide--accessories-a { top: 105px; }
  .slide--accessories-b { top: 923px; }
  .slide--repair { top: 1588px; }

  .slide--accessories-a .hero, .slide--accessories-b .hero {
    position: absolute; inset: 38px 0 0 0;
    background: linear-gradient(160deg, var(--cyan-1) 0%, var(--cyan-2) 60%, #36c6ea 100%);
  }
  .slide--repair .hero {
    position: absolute; inset: 38px 0 0 0; background: var(--repair-bg);
  }

  .topbar {
    position: absolute; left: 0; top: 0; width: 100%; height: 38px; background: var(--bar);
    font-size: 12.5px; color: var(--ink-soft);
  }
  .topbar .contacts { position: absolute; left: 87px; top: 11px; display: flex; align-items: center; gap: 5px; }
  .topbar .contacts b { color: var(--ink); font-weight: 500; }
  .topbar .links span { position: absolute; top: 11px; color: var(--ink); font-size: 13px; }
  .topbar .status { left: 716px; }
  .topbar .lang-est { left: 902px; }
  .topbar .lang-rus { left: 959px; }

  .brand {
    position: absolute; left: 87px; top: 48px; display: flex; align-items: center; gap: 8px;
    font-weight: 700; font-size: 38px; color: #ffffff; letter-spacing: -0.5px;
  }
  .brand .mark { width: 14px; height: 14px; border-radius: 50%; background: currentColor; }
  .slide--repair .brand { color: var(--ink); }

  .nav { position: absolute; top: 67px; left: 0; width: 100%; font-size: 15px; font-weight: 500; color: #ffffff; }
  .nav span { position: absolute; white-space: nowrap; }
  .nav .home { left: 469px; color: var(--ink); }
  .nav .prices { left: 538px; }
  .nav .news { left: 708px; }
  .nav .broken { left: 770px; }
  .nav .contact { left: 929px; }
  .slide--repair .nav { color: var(--ink); }

  .headline {
    position: absolute; left: 81px; top: 214px; font-size: 42px; line-height: 44px;
    font-weight: 500; color: #ffffff;
  }
  .cta {
    position: absolute; left: 81px; top: 330px; width: 147px; height: 49px; border-radius: 25px;
    border: 2px solid #ffffff; color: #ffffff; font-size: 16px; font-weight: 500;
    display: flex; align-items: center; justify-content: center;
  }
  .dots { position: absolute; left: 81px; top: 470px; display: flex; gap: 12px; }
  .dots i { width: 8px; height: 8px; border-radius: 50%; background: #ffffff; display: block; }
  .dots i.current { background: transparent; border: 1.5px solid #ffffff; }

  .product-photo {
    position: absolute; left: 520px; top: 160px; width: 545px; height: 393px;
    background:
      radial-gradient(ellipse at 70% 75%, rgba(150,95,60,0.55) 0%, rgba(205,175,150,0.35) 35%, rgba(255,255,255,0) 65%),
      radial-gradient(ellipse at 95% 70%, rgba(225,245,248,0.7) 0%, rgba(255,255,255,0) 45%),
      radial-gradient(ellipse at 55% 40%, rgba(255,255,255,0.45) 0%, rgba(255,255,255,0) 50%);
  }

  .badge {
    position: absolute; border-radius: 50%; display: flex; align-items: center; justify-content: center;
    text-align: center; font-family: "Yanone Kaffeesatz", sans-serif; font-weight: 300;
    font-size: 26px; line-height: 30px; color: var(--cyan-text);
  }
  .badge--light { background: var(--badge-light); box-shadow: 0 3px 10px rgba(0,0,0,0.12); }
  .badge--dark { background: var(--badge-dark); box-shadow: 0 4px 12px rgba(0,0,0,0.25); }
  .badge--l { width: 150px; height: 150px; }
  .badge--m { width: 117px; height: 117px; }
  .badge--s { width: 103px; height: 103px; }
  .b-protectors { left: 698px; top: 102px; }
  .b-chargers { left: 594px; top: 270px; }
  .b-covers { left: 456px; top: 296px; }
  .b-headphones { left: 426px; top: 430px; }
  .b-sell { left: 924px; top: 385px; }

  .repair-photo {
    position: absolute; left: 0; top: 66px; width: 706px; height: 487px;
    background:
      radial-gradient(ellipse at 25% 35%, rgba(255,255,255,0.9) 0%, rgba(255,255,255,0) 45%),
      radial-gradient(ellipse at 45% 88%, rgba(60,80,110,0.55) 0%, rgba(120,140,165,0.25) 35%, rgba(238,241,244,0) 65%),
      linear-gradient(90deg, #dfe4ea 0%, #e9edf1 60%, rgba(238,241,244,0) 100%);
  }
  .repair-title {
    position: absolute; left: 626px; top: 165px; font-size: 40px; line-height: 48px;
    font-weight: 500; color: #222222;
  }
  .slide--repair .cta { left: 626px; top: 282px; border-color: var(--cyan-text); color: var(--cyan-text); background: #ffffff; }
  .slide--repair .dots { left: 627px; top: 370px; }
  .slide--repair .dots i { background: #9aa1a8; }
  .slide--repair .dots i.current { background: var(--cyan-text); border: none; }
  .b-motherboard { left: 340px; top: 125px; }
  .b-swap { left: 166px; top: 212px; }
  .b-battery { left: 444px; top: 314px; width: 133px; height: 133px; }
  .b-heavy { left: 83px; top: 378px; }
</style>
</head>
<body>

  <section class="slide slide--accessories-a">
    <div class="hero"></div>
    <div class="topbar">
      <div class="contacts">
        <svg width="12" height="12" viewBox="0 0 24 24" aria-hidden="true"><path fill="#222" d="M6.6 10.8c1.4 2.8 3.8 5.1 6.6 6.6l2.2-2.2c.3-.3.7-.4 1-.2 1.1.4 2.3.6 3.6.6.6 0 1 .4 1 1V20c0 .6-.4 1-1 1C10.6 21 3 13.4 3 4c0-.6.4-1 1-1h3.5c.6 0 1 .4 1 1 0 1.3.2 2.5.6 3.6.1.3 0 .7-.2 1l-2.3 2.2z"/></svg>
        <span>Overseas <b>+372 500 111 22</b> | Department store <b>+372 5000 1234</b></span>
      </div>
      <div class="links"><span class="status">Check the repair status</span><span class="lang-est">Est</span><span class="lang-rus">Rus</span></div>
    </div>
    <div class="brand"><span class="mark"></span>Nutikoda</div>
    <nav class="nav"><span class="home">Home</span><span class="prices">Price list of services</span><span class="news">News</span><span class="broken">In case it is broken</span><span class="contact">Contact</span></nav>
    <div class="product-photo" role="img" aria-label="Phone cases, earphones and charging cables"></div>
    <h1 class="headline">Mobile Phones and Tablet<br>Accessories</h1>
    <div class="cta">Learn More</div>
    <div class="dots"><i class="current"></i><i></i><i></i><i></i></div>
    <div class="badge badge--light badge--l b-protectors">Screen<br>Protectors and<br>Saftey Glasses</div>
    <div class="badge badge--dark badge--m b-chargers">Chargers<br>and Cables</div>
    <div class="badge badge--light badge--s b-covers">Covers</div>
    <div class="badge badge--dark badge--m b-headphones">Headphones</div>
    <div class="badge badge--dark badge--m b-sell">sell<br>Accessories</div>
  </section>

  <section class="slide slide--accessories-b">
    <div class="hero"></div>
    <div class="topbar">
      <div class="contacts">
        <svg width="12" height="12" viewBox="0 0 24 24" aria-hidden="true"><path fill="#222" d="M6.6 10.8c1.4 2.8 3.8 5.1 6.6 6.6l2.2-2.2c.3-.3.7-.4 1-.2 1.1.4 2.3.6 3.6.6.6 0 1 .4 1 1V20c0 .6-.4 1-1 1C10.6 21 3 13.4 3 4c0-.6.4-1 1-1h3.5c.6 0 1 .4 1 1 0 1.3.2 2.5.6 3.6.1.3 0 .7-.2 1l-2.3 2.2z"/></svg>
        <span>Overseas <b>+372 500 111 22</b> | Department store <b>+372 5000 1234</b></span>
      </div>
      <div class="links"><span class="status">Check the repair status</span><span class="lang-est">Est</span><span class="lang-rus">Rus</span></div>
    </div>
    <div class="brand"><span class="mark"></span>Nutikoda</div>
    <nav class="nav"><span class="home">Home</span><span class="prices">Price list of services</span><span class="news">News</span><span class="broken">In case it is broken</span><span class="contact">Contact</span></nav>
    <div class="product-photo" role="img" aria-label="Phone cases, earphones and charging cables"></div>
    <h1 class="headline">Mobile Phones and Tablet<br>Accessories</h1>
    <div class="cta">Learn More</div>
    <div class="dots"><i class="current"></i><i></i><i></i><i></i></div>
    <div class="badge badge--light badge--l b-protectors">Screen<br>Protectors and<br>Saftey Glasses</div>
    <div class="badge badge--dark badge--m b-chargers">Chargers<br>and Cables</div>
    <div class="badge badge--light badge--s b-covers">Covers</div>
    <div class="badge badge--dark badge--m b-headphones">Headphones</div>
    <div class="badge badge--dark badge--m b-sell">sell<br>Accessories</div>
  </section>

  <section class="slide slide--repair">
    <div class="hero"></div>
    <div class="repair-photo" role="img" aria-label="Gloved hand repairing an opened smartphone with tweezers"></div>
    <div class="topbar">
      <div class="contacts">
        <svg width="12" height="12" viewBox="0 0 24 24" aria-hidden="true"><path fill="#222" d="M6.6 10.8c1.4 2.8 3.8 5.1 6.6 6.6l2.2-2.2c.3-.3.7-.4 1-.2 1.1.4 2.3.6 3.6.6.6 0 1 .4 1 1V20c0 .6-.4 1-1 1C10.6 21 3 13.4 3 4c0-.6.4-1 1-1h3.5c.6 0 1 .4 1 1 0 1.3.2 2.5.6 3.6.1.3 0 .7-.2 1l-2.3 2.2z"/></svg>
        <span>Overseas <b>+372 500 111 22</b> | Department store <b>+372 5000 1234</b></span>
      </div>
      <div class="links"><span class="status">Check the repair status</span><span class="lang-est">Est</span><span class="lang-rus">Rus</span></div>
    </div>
    <div class="brand"><span class="mark"></span>Nutikoda</div>
    <nav class="nav"><span class="home">Home</span><span class="prices">Price list of services</span><span class="news">News</span><span class="broken">In case it is broken</span><span class="contact">Contact</span></nav>
    <h1 class="repair-title">REPAIR OF MOBILE<br>PHONES</h1>
    <div class="cta">Learn More</div>
    <div class="dots"><i class="current"></i><i></i><i></i><i></i></div>
    <div class="badge badge--light badge--l b-motherboard">Motherboard<br>replacement</div>
    <div class="badge badge--dark badge--m b-swap">Screen<br>Swap</div>
    <div class="badge badge--dark b-battery">Fast battery<br>replacement</div>
    <div class="badge badge--light badge--s b-heavy">Heavy<br>repair</div>
  </section>

</body>
</html>
```